Paperwell Solutions Services Flyer

Create a 2 sided A4 flyer/PDF of the services we offer and a description of each etc.
Details can be found at: https://www.paperwell-solutions.co.uk/
Main services: Document Scanning, Invoice Processing and other services we offer.

Industry/Entity Type

Document Management

Font styles to use
Other font styles liked:
• Montserrat

Colors

Designer to choose colors to be used in the design.

Requirements
Must have
• Document Scanning, Box Storage, Invoice Processing, Book Scanning, Large format scanning
Nice to have
• Colourful d/s flyer listing our services with a brief description on each

```html
<!DOCTYPE html>
<html lang="en">
<head>
<meta charset="utf-8">
<title>Paperwell Solutions – Document Automation Services</title>
<link href="https://fonts.googleapis.com/css2?family=Montserrat:wght@400;500;600;700&display=swap" rel="stylesheet">
<style>
  :root{
    --red:#c8161d;
    --red-dark:#8e1118;
    --blue:#4f8bc0;
    --navy:#1d4a66;
    --ink:#1a1a1a;
    --backdrop:#dcdcdc;
    --white:#ffffff;
  }
  *{box-sizing:border-box;margin:0;padding:0}
  html,body{width:1200px;height:847px;overflow:hidden;background:var(--backdrop);font-family:"Montserrat",sans-serif;color:var(--ink)}
  .page{position:absolute;top:16px;width:576px;height:814px;background:var(--white);overflow:hidden}
  .page-front{left:16px}
  .page-back{left:608px}

  /* front */
  .front-art{position:absolute;inset:0}
  .brand{position:absolute;left:48px;top:0;width:132px;height:72px;background:var(--white);border-radius:0 0 10px 10px;display:flex;align-items:center;justify-content:center;gap:6px}
  .brand-name{color:var(--red);font-weight:700;font-size:15px;line-height:1.05;text-align:left}
  .brand-dot{width:8px;height:8px;background:var(--red);border-radius:50%}
  .front-title{position:absolute;left:0;right:0;top:88px;text-align:center;color:var(--white);font-weight:700;font-size:28.5px;letter-spacing:.2px;text-shadow:0 1px 3px rgba(0,0,0,.25)}
  .equipment{position:absolute;top:139px;width:94px;height:94px;border-radius:50%;background:radial-gradient(circle at 50% 55%,#9a9a9a 0%,#d8d8d8 45%,#ffffff 70%);border:2px solid var(--white)}
  .eq-1{left:74px}.eq-2{left:184px}.eq-3{left:298px}.eq-4{left:409px}

  .services-panel{position:absolute;left:71px;top:261px;width:436px}
  .panel-head{height:57px;background:var(--red);border-radius:8px 8px 0 0;color:var(--white);font-weight:700;font-size:21px;text-align:center;padding-top:12px}
  .service-grid{position:absolute;left:0;top:44px;width:436px;display:grid;grid-template-columns:repeat(3,130px);grid-template-rows:repeat(3,125px);column-gap:23px;row-gap:12px}
  .service-card{background:var(--white);border:1.5px solid var(--red);border-radius:13px;display:flex;flex-direction:column;align-items:center;padding-top:10px}
  .service-icon{width:66px;height:56px;border-radius:10px;background:linear-gradient(135deg,var(--navy),#3c7aa3 60%,var(--red))}
  .service-label{margin-top:8px;color:var(--red);font-weight:700;font-size:15.5px;line-height:1;text-align:center}

  .contact{position:absolute;left:91px;top:727px;font-size:10.5px;line-height:14px}
  .contact-row{display:flex;align-items:center;gap:6px}
  .contact-row svg{width:12px;height:12px}
  .address{position:absolute;left:252px;top:724px;font-size:10.5px;line-height:12px;display:flex;gap:8px}
  .address svg{width:10px;height:12px;margin-top:1px}
  .certs{position:absolute;left:382px;top:722px;width:112px;text-align:center}
  .badges{display:flex;justify-content:center;gap:8px;align-items:center;height:30px}
  .badge-round{width:26px;height:26px;border-radius:50%;border:2px solid #555}
  .badge-square{width:22px;height:26px;border:1.5px solid #555}
  .badge-bar{width:28px;height:12px;background:#555;border-radius:2px}
  .cert-no{font-weight:700;font-size:9px;margin-top:5px}
  .cert-std{font-size:9px;margin-top:2px}

  /* back */
  .back-head{position:absolute;left:0;top:0;width:576px;height:173px;background:var(--blue);color:var(--white);text-align:center}
  .back-title{font-weight:600;font-size:24px;margin-top:38px}
  .back-intro{font-size:12.3px;line-height:14.5px;width:450px;margin:8px auto 0}
  .service-group{position:absolute;left:74px;width:427px;height:195px;border:1.5px solid var(--red);border-radius:10px}
  .group-1{top:190px}.group-2{top:391px}.group-3{top:592px}
  .service-item{position:absolute;left:34px;width:380px}
  .item-icon{position:absolute;left:0;top:0;width:53px;height:53px;border-radius:50%;border:1.5px solid var(--red);background:radial-gradient(circle,#3c7aa3 0%,var(--navy) 35%,#e9eef3 38%,var(--white) 60%)}
  .item-body{position:absolute;left:62px;top:7px;width:301px}
  .item-title{color:var(--red);font-weight:700;font-size:15.5px;line-height:1}
  .item-text{font-size:7.9px;line-height:8.7px;margin-top:3px;text-align:justify}
  .row-1{top:6px}.row-2{top:68px}.row-3{top:130px}
</style>
</head>
<body>

<section class="page page-front">
  <svg class="front-art" viewBox="0 0 576 814" width="576" height="814">
    <defs>
      <linearGradient id="archive" x1="0" y1="0" x2="0" y2="1">
        <stop offset="0" stop-color="#6f8fb5"/>
        <stop offset=".5" stop-color="#a9c2de"/>
        <stop offset="1" stop-color="#7d9cc0"/>
      </linearGradient>
    </defs>
    <path role="img" aria-label="Photo of a records archive aisle lined with storage boxes" fill="url(#archive)" d="M0 0H576V250C430 248 330 258 250 262C150 262 70 230 0 120Z"/>
    <path fill="var(--red-dark)" d="M0 120C60 240 160 268 260 266C360 262 460 246 576 240V330C470 300 360 296 250 300C150 305 60 330 0 360Z"/>
    <path fill="var(--red)" d="M0 150C60 270 170 290 280 280C380 270 470 262 576 262V340C470 320 360 316 250 320C150 326 60 350 0 380Z"/>
    <path fill="var(--white)" d="M0 380C80 340 190 300 300 290C400 282 480 290 576 318V814H0Z"/>
    <path fill="var(--red)" d="M0 766C90 772 180 786 300 814H0Z"/>
    <path fill="var(--red-dark)" d="M0 782C70 789 140 800 210 814H0Z"/>
    <path fill="var(--red)" d="M576 720C540 770 500 800 470 814H576Z"/>
  </svg>

  <div class="brand"><span class="brand-dot"></span><span class="brand-name">Paperwell<br>Solutions</span></div>
  <h1 class="front-title">Document Automation Services</h1>

  <div class="equipment eq-1" role="img" aria-label="Photo of an overhead book scanner station"></div>
  <div class="equipment eq-2" role="img" aria-label="Photo of a production document scanner"></div>
  <div class="equipment eq-3" role="img" aria-label="Photo of a high-volume scanning machine"></div>
  <div class="equipment eq-4" role="img" aria-label="Photo of a large format scanner"></div>

  <div class="services-panel">
    <div class="panel-head">What can we do for you?</div>
    <div class="service-grid">
      <div class="service-card"><div class="service-icon" role="img" aria-label="Illustration of scanned documents"></div><p class="service-label">Document<br>Scanning</p></div>
      <div class="service-card"><div class="service-icon" role="img" aria-label="Illustration of documents with gears"></div><p class="service-label">Document<br>Processing</p></div>
      <div class="service-card"><div class="service-icon" role="img" aria-label="Illustration of an archive box"></div><p class="service-label">Box<br>Storage</p></div>
      <div class="service-card"><div class="service-icon" role="img" aria-label="Illustration of shredder blades"></div><p class="service-label">Secure<br>Document<br>Destruction</p></div>
      <div class="service-card"><div class="service-icon" role="img" aria-label="Illustration of a document folder"></div><p class="service-label">Document<br>Management<br>Systems</p></div>
      <div class="service-card"><div class="service-icon" role="img" aria-label="Illustration of a computer receiving digital mail"></div><p class="service-label">Digital<br>Mailroom</p></div>
      <div class="service-card"><div class="service-icon" role="img" aria-label="Illustration of a film reel"></div><p class="service-label">Microfilm<br>Digitisation</p></div>
      <div class="service-card"><div class="service-icon" role="img" aria-label="Illustration of linked gears"></div><p class="service-label">Workflow<br>Systems</p></div>
      <div class="service-card"><div class="service-icon" role="img" aria-label="Illustration of a large sheet being scanned"></div><p class="service-label">Large Format<br>Scanning</p></div>
    </div>
  </div>

  <div class="contact">
    <div class="contact-row">
      <svg viewBox="0 0 24 24"><path fill="#222" d="M6.6 10.8a15 15 0 0 0 6.6 6.6l2.2-2.2a1 1 0 0 1 1-.25 11 11 0 0 0 3.6.6 1 1 0 0 1 1 1V20a1 1 0 0 1-1 1A17 17 0 0 1 3 4a1 1 0 0 1 1-1h3.5a1 1 0 0 1 1 1c0 1.25.2 2.45.6 3.6a1 1 0 0 1-.25 1z"/></svg>
      <span>01632 960418</span>
    </div>
    <div class="contact-row">
      <svg viewBox="0 0 24 24"><circle cx="12" cy="12" r="10" fill="#222"/><path d="M2 12h20M12 2c3 3 3 17 0 20M12 2c-3 3-3 17 0 20" stroke="#fff" stroke-width="1.4" fill="none"/></svg>
      <span>paperwell-solutions.co.uk</span>
    </div>
  </div>

  <div class="address">
    <svg viewBox="0 0 20 24"><path fill="#222" d="M10 0a8 8 0 0 0-8 8c0 6 8 16 8 16s8-10 8-16a8 8 0 0 0-8-8zm0 11a3 3 0 1 1 0-6 3 3 0 0 1 0 6z"/></svg>
    <p>Harlow<br>Court,<br>Millbrook Lane<br>Redfield, West<br>Sussex<br>RH99 4QT</p>
  </div>

  <div class="certs">
    <div class="badges"><span class="badge-round"></span><span class="badge-square"></span><span class="badge-bar"></span></div>
    <p class="cert-no">Certificate No. 20457</p>
    <p class="cert-std">ISO 9001 ISO 27001</p>
  </div>
</section>

<section class="page page-back">
  <header class="back-head">
    <h2 class="back-title">Document Automation Services</h2>
    <p class="back-intro">Paperwell Solutions is a trusted provider of document scanning, storage and processing services. Since 1989, we’ve helped organisations of all sizes take control of their paperwork – whether it’s hardcopy or digital. With a focus on security, reliability and efficiency, we turn labour intensive challenges into streamlined solutions helping you reduce costs, improve workflows and grow your business.</p>
  </header>

  <div class="service-group group-1">
    <div class="service-item row-1"><div class="item-icon" role="img" aria-label="Document scanning icon"></div><div class="item-body"><h3 class="item-title">Document Scanning</h3><p class="item-text">Digitise your physical files with our high-volume document scanning services. We use advanced technology to ensure precision and efficiency in converting paper documents, files, and media into digital formats such as PDF, making information instantly accessible and easy to manage.</p></div></div>
    <div class="service-item row-2"><div class="item-icon" role="img" aria-label="Document processing icon"></div><div class="item-body"><h3 class="item-title">Document Processing</h3><p class="item-text">Streamline operations with customised document and invoice processing systems. Our automation solutions replace manual workflows, reduce human error, and optimise paper-based processes, saving time and cutting costs.</p></div></div>
    <div class="service-item row-3"><div class="item-icon" role="img" aria-label="Box storage icon"></div><div class="item-body"><h3 class="item-title">Box Storage</h3><p class="item-text">Secure your critical records with our document storage services. We provide highly regulated storage facilities and robust cloud platforms, ensuring reliable retention of both physical and digital records for your peace of mind.</p></div></div>
  </div>

  <div class="service-group group-2">
    <div class="service-item row-1"><div class="item-icon" role="img" aria-label="Secure destruction icon"></div><div class="item-body"><h3 class="item-title">Secure Document Destruction</h3><p class="item-text">Dispose of obsolete or sensitive documents securely with our certified destruction services. Our compliant processes ensure that your materials are destroyed in line with stringent regulatory requirements.</p></div></div>
    <div class="service-item row-2"><div class="item-icon" role="img" aria-label="Document management icon"></div><div class="item-body"><h3 class="item-title">Document Management Systems</h3><p class="item-text">Centralise and streamline your information with our feature-rich document management software. Consolidate documents from across your organisation into a single, searchable repository, enhancing accessibility and productivity.</p></div></div>
    <div class="service-item row-3"><div class="item-icon" role="img" aria-label="Digital mailroom icon"></div><div class="item-body"><h3 class="item-title">Digital Mailroom</h3><p class="item-text">Future-proof your business with our digital mailroom solutions. We digitise incoming mail and automate workflows, replacing outdated paper-based systems with efficient, modern digital processes.</p></div></div>
  </div>

  <div class="service-group group-3">
    <div class="service-item row-1"><div class="item-icon" role="img" aria-label="Microfilm icon"></div><div class="item-body"><h3 class="item-title">Microfilm Digitisation</h3><p class="item-text">Preserve and access historical data with our expert microfilm digitisation services. We convert microfilm records into searchable, high-quality digital formats, ensuring the longevity and usability of your archives.</p></div></div>
    <div class="service-item row-2"><div class="item-icon" role="img" aria-label="Workflow systems icon"></div><div class="item-body"><h3 class="item-title">Workflow Systems</h3><p class="item-text">Transform your operations with our tailored workflow systems. These solutions automate tasks, reduce manual intervention, and enable seamless information flow across your organisation, enhancing collaboration and efficiency.</p></div></div>
    <div class="service-item row-3"><div class="item-icon" role="img" aria-label="Large format scanning icon"></div><div class="item-body"><h3 class="item-title">Large Format Scanning</h3><p class="item-text">Our specialised large-format and book scanning services digitise oversized materials and bound volumes such as blueprints, maps, and posters with precision and clarity, ensuring no detail is lost.</p></div></div>
  </div>
</section>

</body>
</html>
```